skyPARLOR Helicopter Tour WordPress Website Design

SkyPARLOR (skyparlor-example.com) is a premium helicopter tour company offering scenic flights in two Florida cities: Tampa and Sarasota. We are seeking a full Wordpress website redesign that is modern, upbeat, inviting, and highly conversion‑focused. The new site should feel energetic and trustworthy, reflect the excitement of helicopter sightseeing, and maintain our recognizable SkyPARLOR color palette—while updating the overall look to feel fresh, clean, and current.
The website must be SEO‑friendly, mobile‑optimized, and easy to navigate. It should highlight our 5‑star customer reviews, showcase our tours clearly, and integrate seamlessly with TrailDock for instant online booking. The design should support a premium aviation experience while remaining friendly and accessible to tourists, families, couples, and adventure seekers.

These elements are essential and must be included in the design:

Brand & UX:
- Modern, upbeat, inviting design
- SEO‑friendly structure and layout
- Easy navigation and clear user flow
- Light grey “SP” background logo watermark (as used on current site)
- Clean, aviation‑inspired typography and layout

Conversion Features:
- Instant booking above the fold (TrailDock integration)
- Live Orbin Ratings carousel
- Tour comparison table (duration, route, price, etc.)
- FAQ expandable section
- Gift Cards page (highlighted as a major offering)
- What to Expect timeline (Arrive → Check‑In → Safety Briefing → Flight → Photos)
- Weather transparency widget (clear messaging about weather‑dependent flights

Content Structure:
- Separate pages for Tampa, Sarasota, and Gender Reveal Flights
- Pilot/Team profiles with short bios
- Highlighted features:
- Doors‑Off option
- Sunset flights
- Romantic packages
- Champagne add‑ons

Colors:
Use the existing SkyPARLOR palette as the foundation, but modernize it.
- Background: Clean with the light grey “SP” watermark integrated tastefully.
The overall color direction should feel bright, premium, energetic, and trustworthy

Target Market(s)

Tourists visiting Tampa or Sarasota, Families looking for memorable activities, Couples seeking romantic experiences (sunset flights, proposals, anniversaries), Adventure seekers and content creators, Locals celebrating birthdays, holidays, or special occasions, Gender reveal clients looking for a unique aerial reveal experience

Industry/Entity Type

Travel & Tourism / Aviation / Helicopter Tours / Experience‑based Activities

Requirements
Must have
• These elements are essential and must be included in the design: Brand & UX - Modern, upbeat, inviting design / SEO‑friendly structure and layout / Easy navigation and clear user flow / Light grey “SP” background logo watermark (as used on current site) / Clean, aviation‑inspired typography and layout
Nice to have
• Interactive route map showing flight paths / Subtle motion or parallax effects in hero sections / Animated icons or micro‑interactions / Social media integration (Instagram grid, TikTok clips) / Sticky mobile booking bar / Video header or short aerial footage loop / Subtle aviation‑themed graphic elements (rotor blur, sky gradients, etc.
Should not have
• No dark, heavy, or overly moody themes / No outdated fonts or overly playful typography / No cluttered layouts or excessive text blocks / No stocky, generic tourism imagery / No slow‑loading animations or heavy effects that hurt SEO

```html
<!DOCTYPE html>
<html lang="en">
<head>
<meta charset="utf-8">
<title>skyPARLOR – Florida Helicopter Tours</title>
<link rel="stylesheet" href="https://fonts.googleapis.com/css2?family=Michroma&family=Montserrat:wght@400;500;600;700&display=swap">
<style>
:root{
  --blue:#1f5ca8;
  --blue-dark:#184d90;
  --blue-soft:#7ea3d6;
  --ink:#1b1b1b;
  --grey:#6b6b6b;
  --line:#d9dde4;
  --pale:#eef3fb;
  --light:#f3f3f3;
  --white:#ffffff;
  --black:#0d0d0d;
  --star:#f4b400;
}
*{box-sizing:border-box;margin:0;padding:0}
html,body{width:1200px;height:4054px;overflow:hidden;background:var(--white)}
body{font-family:"Montserrat",sans-serif;color:var(--ink);position:relative}
.abs{position:absolute}
.title{font-family:"Michroma",sans-serif;font-size:32px;letter-spacing:.5px;text-align:center;left:0;width:1200px;color:var(--ink)}
.bar{height:3px;width:96px;background:var(--blue-soft);left:552px}
.btn{display:flex;align-items:center;justify-content:center;gap:8px;border-radius:30px;background:var(--blue);color:var(--white);font-weight:700;font-size:14px;letter-spacing:.3px}
.chev{width:7px;height:10px}

/* header */
.site-header{top:0;left:0;width:1200px;height:95px;background:var(--white)}
.brand{left:143px;top:22px;font-size:28px;font-weight:700;color:var(--blue);letter-spacing:.5px;display:flex;align-items:center;gap:10px}
.brand i{width:14px;height:14px;border-radius:50%;background:var(--blue);display:block}
.topbar{right:145px;top:14px;display:flex;gap:20px;font-size:12px;color:#333}
.topbar span{display:flex;align-items:center;gap:6px}
.nav{right:145px;top:57px;display:flex;gap:32px;font-size:14px;font-weight:500}
.nav .on{color:var(--blue)}

/* hero */
.hero{top:95px;left:0;width:1200px;height:570px;background:linear-gradient(160deg,#9ccbd3 0%,#b9dce0 40%,#8fbcc6 75%,#7aaab8 100%)}
.hero-curve{top:560px;left:0}
.hero h1{left:143px;top:198px;font-family:"Michroma",sans-serif;font-weight:400;font-size:52px;line-height:80px;color:var(--ink)}
.hero h1 .sky{color:var(--blue)}
.hero-text{left:143px;top:356px;width:520px;font-size:17px;line-height:30px;color:#222}
.hero .btn{left:143px;top:447px;width:281px;height:47px;font-size:15px}
.dots{left:575px;top:614px;display:flex;gap:4px}
.dots i{width:9px;height:9px;border:1.5px solid #333;border-radius:50%;display:block}
.dots i.on{background:var(--blue);border-color:var(--blue)}

/* about */
.about-photo{left:143px;top:688px;width:441px;height:441px;border-radius:50%;background:radial-gradient(circle at 40% 40%,#c9a27e,#6e5a4a 55%,#3b3b3b)}
.about-badge{left:452px;top:945px;width:148px;height:148px;border-radius:50%;background:var(--white);display:flex;align-items:center;justify-content:center;font-family:"Michroma",sans-serif;font-size:40px;color:#6a6a6a}
.about h2{left:655px;top:736px;font-family:"Michroma",sans-serif;font-weight:400;font-size:32px}
.about .bar{left:655px;top:786px}
.about-lede{left:655px;top:822px;width:400px;font-size:16px;line-height:27px}
.about-copy{left:655px;top:882px;width:405px;font-size:13px;line-height:23.5px;color:var(--grey)}
.about .btn{left:655px;top:1039px;width:152px;height:43px}

/* tours */
.tours{top:1189px;left:0;width:1200px;height:551px;background:var(--pale)}
.tours .title{top:1252px}
.tours .bar{top:1305px}
.tours-sub{top:1333px;left:0;width:1200px;text-align:center;font-size:13px}
.arrow{width:20px;height:28px}
.tour-card{top:1381px;height:279px;border-radius:16px;overflow:hidden}
.tour-card .panel{position:absolute;left:22px;right:22px;top:21px;bottom:19px;border-radius:14px;background:rgba(255,255,255,.78);text-align:center}
.pill{display:inline-flex;align-items:center;gap:6px;margin-top:48px;background:var(--blue-soft);color:var(--white);font-size:11px;border-radius:14px;padding:4px 16px}
.tour-card h3{font-weight:500;font-size:16px;margin-top:14px}
.tour-card p{font-size:13px;line-height:23px;margin-top:6px;padding:0 40px}
.tour-card .book{display:inline-flex;align-items:center;gap:8px;color:var(--blue);font-weight:700;font-size:14px;margin-top:12px}

/* features */
.features{top:1740px;left:0;width:1200px;height:460px;background:linear-gradient(120deg,#1d5aa6,#2563b0 50%,#1b559e)}
.features .title{top:1795px;color:var(--white)}
.features .bar{top:1850px;background:#8fb1de}
.feature{top:1888px;width:250px;text-align:center;color:var(--white)}
.feature svg{height:74px;width:90px}
.feature h4{font-weight:500;font-size:17px;margin-top:16px}
.feature p{font-size:13px;line-height:23px;margin-top:8px}
.features .btn{left:468px;top:2099px;width:247px;height:43px;background:var(--white);color:var(--blue);font-size:14px}

/* reviews */
.faint-scene{top:2560px;left:0;width:1200px;height:668px;background:linear-gradient(180deg,rgba(255,255,255,0) 0%,#e9e9e9 30%,#f2f2f2 70%,#ffffff 100%)}
.reviews .title{top:2275px}
.reviews .bar{top:2328px}
.review{top:2373px;width:296px;height:182px;background:#f1f1f1;border-radius:14px;padding:46px 20px 0 20px}
.review .q{position:absolute;left:16px;top:20px;font-family:Georgia,serif;font-size:38px;line-height:30px;color:#c4c4c4}
.review .qe{left:auto;right:14px;top:138px}
.review .mark{position:absolute;right:12px;top:12px;width:22px;height:22px;border-radius:50%;border:3px solid var(--blue)}
.review p{font-size:12.5px;line-height:23.5px;color:#555;text-align:justify}
.person{top:2573px;display:flex;gap:14px;align-items:flex-start}
.avatar{width:56px;height:56px;border-radius:50%;background:linear-gradient(135deg,#d6c9bd,#8d7a6b)}
.person b{display:block;font-weight:500;font-size:17px;margin-top:8px}
.stars{color:var(--star);font-size:13px;letter-spacing:1px}

/* faq */
.faq .title{top:2703px}
.faq .bar{top:2757px}
.faq-item{left:143px;width:912px;height:49px;border:1px solid var(--line);border-radius:8px;background:var(--white);padding:0 22px;display:flex;align-items:center;justify-content:space-between;font-size:15px}
.faq-item.open{height:110px;background:var(--blue);border-color:var(--blue);color:var(--white);display:block;padding-top:15px}
.faq-item.open .row{display:flex;justify-content:space-between}
.faq-item.open p{font-size:12.5px;line-height:23px;margin-top:8px;padding-right:40px}
.more{top:3131px;left:0;width:1200px;text-align:center;font-size:13.5px;font-weight:700;color:var(--blue)}
.more span{text-decoration:underline}

/* contact */
.contact{top:3228px;left:0;width:1200px;height:560px;background:var(--light)}
.watermark{top:3330px;left:300px;width:600px;text-align:center;font-family:"Michroma",sans-serif;font-size:300px;line-height:420px;color:#e6e6e6}
.contact .title{top:3287px}
.contact .bar{top:3341px}
.field{left:192px;width:391px;height:54px;background:var(--white);border:1px solid var(--line);border-radius:8px;font-size:12px;color:#555;padding:19px 22px 0}
.field.msg{left:616px;width:390px;height:187px}
.contact .btn{left:520px;top:3614px;width:160px;height:43px}

/* footer */
.site-footer{top:3724px;left:0;width:1200px;height:330px}
.footer-brand{left:143px;top:3860px;font-size:28px;font-weight:700;color:#3b7bd0;letter-spacing:.5px}
.fcol h5{font-size:16px;font-weight:600;color:#5b95dd;margin-bottom:14px}
.fcol li{list-style:none;font-size:13px;line-height:24px;color:#e8e8e8}
.fcol .ci{display:flex;align-items:center;gap:9px;margin-bottom:16px}
.ring{width:26px;height:26px;border:1.5px solid #e8e8e8;border-radius:50%;display:flex;align-items:center;justify-content:center}
.socials{display:flex;gap:7px}
.socials i{width:26px;height:26px;border:1.5px solid #e8e8e8;border-radius:50%;display:block}
.copyright{top:4022px;left:0;width:1200px;text-align:center;font-size:13px;color:#e8e8e8}
</style>
</head>
<body>

<!-- Header -->
<header class="abs site-header">
  <div class="abs brand"><i></i>skyPARLOR</div>
  <div class="abs topbar">
    <span><svg width="13" height="10" viewBox="0 0 13 10"><rect width="13" height="10" rx="1" fill="#1f5ca8"/><path d="M0 1l6.5 5L13 1" stroke="#fff" fill="none"/></svg>info@skyparlor-example.com</span>
    <span><svg width="11" height="11" viewBox="0 0 24 24"><path fill="#1f5ca8" d="M6.6 10.8a15 15 0 0 0 6.6 6.6l2.2-2.2a1 1 0 0 1 1-.25 11 11 0 0 0 3.6.6 1 1 0 0 1 1 1V20a1 1 0 0 1-1 1A17 17 0 0 1 3 4a1 1 0 0 1 1-1h3.5a1 1 0 0 1 1 1 11 11 0 0 0 .6 3.6 1 1 0 0 1-.25 1z"/></svg>(844) 555-0192 | (844) 555-0148</span>
    <span><svg width="13" height="11" viewBox="0 0 13 11"><ellipse cx="6.5" cy="4.5" rx="6.5" ry="4.5" fill="#1f5ca8"/><path d="M2 7l-1 4 4-2.5z" fill="#1f5ca8"/></svg>FAQS</span>
  </div>
  <nav class="abs nav">
    <span class="on">Home</span><span>Sarasota</span><span>Tampa</span><span>Special Events</span><span>Influencer</span><span>Gift Cards</span><span>Team</span><span>Contact Us</span>
  </nav>
</header>

<!-- Hero -->
<section class="hero-wrap">
  <div class="abs hero" role="img" aria-label="Helicopter with open doors and passengers flying over the Florida coastline"></div>
  <svg class="abs hero-curve" width="1200" height="110" viewBox="0 0 1200 110"><path d="M0 40 Q600 150 1200 30 L1200 110 L0 110 Z" fill="#fff"/></svg>
  <div class="hero">
    <h1 class="abs"><span class="sky">SEE FLORIDA</span><br>FROM THE SKY</h1>
  </div>
  <p class="abs hero-text">Experience breathtaking sightseeing and celebration helicopter flights departing from Florida Harborview Heliport.</p>
  <div class="abs btn" style="left:143px;top:447px;width:281px;height:47px;font-size:15px">BOOK YOUR SKYPARLOR <svg class="chev" viewBox="0 0 7 10"><path d="M1 1l4 4-4 4" stroke="#fff" stroke-width="1.6" fill="none"/></svg></div>
  <div class="abs dots"><i></i><i class="on"></i><i></i><i></i></div>
</section>

<!-- About -->
<section class="about">
  <div class="abs about-photo" role="img" aria-label="Couple toasting with champagne inside a helicopter cabin"></div>
  <div class="abs about-badge">SP</div>
  <h2 class="abs">ABOUT US</h2>
  <div class="abs bar"></div>
  <p class="abs about-lede">Lorem ipsum dolor amet, consectetur adipiscing elit, sed do eiusmod tempor incididunt ut labore</p>
  <p class="abs about-copy">Duis aute irure dolor in reprehenderit in voluptate velit esse cillum dolore eu fugiat nulla pariatur. Excepteur sint occaecat cupidatat non proident, sunt in culpa qui officia deserunt mollit anim id est laborum natus error sit voluptatem accusantium doloremque laudantium, totam rem aperiam,</p>
  <div class="abs btn">READ MORE <svg class="chev" viewBox="0 0 7 10"><path d="M1 1l4 4-4 4" stroke="#fff" stroke-width="1.6" fill="none"/></svg></div>
</section>

<!-- Tours -->
<section>
  <div class="abs tours"></div>
  <h2 class="abs title" style="top:1252px">OUR FLORIDA HELICOPTER TOURS</h2>
  <div class="abs bar" style="top:1305px"></div>
  <p class="abs tours-sub">Take off from Harborview Heliport and see the capital’s most iconic landmarks from the air. Choose the perfect flight duration for your experience.</p>
  <svg class="abs arrow" style="left:88px;top:1506px" viewBox="0 0 20 28"><path d="M15 3L5 14l10 11" stroke="#111" stroke-width="2.5" fill="none"/></svg>
  <svg class="abs arrow" style="left:1091px;top:1506px" viewBox="0 0 20 28"><path d="M5 3l10 11L5 25" stroke="#111" stroke-width="2.5" fill="none"/></svg>

  <article class="abs tour-card" style="left:143px;width:441px;background:linear-gradient(160deg,#9aa3ab,#c9cdd1 50%,#5d8fa0)" role="img" aria-label="Aerial view of Tampa city blocks from a helicopter">
    <div class="panel">
      <span class="pill"><svg width="10" height="10" viewBox="0 0 10 10"><circle cx="5" cy="5" r="4" stroke="#fff" fill="none"/><path d="M5 2.5V5l2 1" stroke="#fff" fill="none"/></svg>25-Min - $ 120.00</span>
      <h3>TAMPA TOWN TOUR</h3>
      <p>Lorem ipsum dolor sit amet, consectetur adipiscing elit, sed do eiusmod tempor incididunt</p>
      <span class="book">BOOK NOW <svg class="chev" viewBox="0 0 7 10"><path d="M1 1l4 4-4 4" stroke="#1f5ca8" stroke-width="1.6" fill="none"/></svg></span>
    </div>
  </article>
  <article class="abs tour-card" style="left:611px;width:444px;background:linear-gradient(170deg,#c9b79c,#7f8c93 45%,#2f4452)" role="img" aria-label="Sarasota downtown skyline and bay at dusk">
    <div class="panel">
      <span class="pill"><svg width="10" height="10" viewBox="0 0 10 10"><circle cx="5" cy="5" r="4" stroke="#fff" fill="none"/><path d="M5 2.5V5l2 1" stroke="#fff" fill="none"/></svg>25-Min - $ 120.00</span>
      <h3>SARASOTA DOWNTOWN TOUR</h3>
      <p>Lorem ipsum dolor sit amet, consectetur adipiscing elit, sed do eiusmod tempor incididunt</p>
      <span class="book">BOOK NOW <svg class="chev" viewBox="0 0 7 10"><path d="M1 1l4 4-4 4" stroke="#1f5ca8" stroke-width="1.6" fill="none"/></svg></span>
    </div>
  </article>
</section>

<!-- Features -->
<section>
  <div class="abs features" role="img" aria-label="Blue tinted helicopter cabin background"></div>
  <h2 class="abs title" style="top:1795px;color:#fff">OUR FEATURES</h2>
  <div class="abs bar" style="top:1850px;background:#8fb1de"></div>

  <div class="abs feature" style="left:103px">
    <svg viewBox="0 0 90 74" fill="none" stroke="#fff" stroke-width="2.2"><path d="M10 10h70M45 10v10"/><path d="M20 30h40a14 14 0 0 1 0 28H34a14 14 0 0 1-14-14z"/><path d="M20 38H4M4 32v12M40 58v10M64 58v10M30 68h46"/><path d="M46 30v14h20"/></svg>
    <h4>Doors-Off option</h4><p>Lorem ipsum dolor sit amet,<br>consectetur adipiscing</p>
  </div>
  <div class="abs feature" style="left:351px">
    <svg viewBox="0 0 90 74" fill="none" stroke="#fff" stroke-width="2.2"><path d="M25 46a20 20 0 0 1 40 0"/><path d="M10 46h70M20 54h50M30 62h30M45 6v12M20 14l7 9M70 14l-7 9M8 32l10 4M82 32l-10 4"/></svg>
    <h4>Sunset flights</h4><p>Lorem ipsum dolor sit amet,<br>consectetur adipiscing</p>
  </div>
  <div class="abs feature" style="left:598px">
    <svg viewBox="0 0 90 74" fill="none" stroke="#fff" stroke-width="2.2"><path d="M45 66C20 48 14 36 14 26a15 15 0 0 1 31-6 15 15 0 0 1 31 6c0 10-6 22-31 40z"/><path d="M34 30c4-4 8-4 11 0 3-4 7-4 11 0"/></svg>
    <h4>Romantic packages</h4><p>Lorem ipsum dolor sit amet,<br>consectetur adipiscing</p>
  </div>
  <div class="abs feature" style="left:847px">
    <svg viewBox="0 0 90 74" fill="none" stroke="#fff" stroke-width="2.2"><path d="M22 20h18l-2 18a7 7 0 0 1-14 0zM31 45v20M24 66h14"/><path d="M52 20h18l-2 18a7 7 0 0 1-14 0zM61 45v20M54 66h14"/><path d="M45 14c-3-4-8-2-6 2l6 5 6-5c2-4-3-6-6-2z"/></svg>
    <h4>Champagne add-ons</h4><p>Lorem ipsum dolor sit amet,<br>consectetur adipiscing</p>
  </div>
  <div class="abs btn" style="left:468px;top:2099px;width:247px;height:43px;background:#fff;color:var(--blue)">BOOK YOUR SKYPARLOR <svg class="chev" viewBox="0 0 7 10"><path d="M1 1l4 4-4 4" stroke="#1f5ca8" stroke-width="1.6" fill="none"/></svg></div>
</section>

<!-- Reviews -->
<section class="reviews">
  <div class="abs faint-scene" role="img" aria-label="Faded photo of smiling guests enjoying a flight"></div>
  <h2 class="abs title" style="top:2275px">WHAT CUSTOMERS ARE SAYING</h2>
  <div class="abs bar" style="top:2328px"></div>
  <svg class="abs arrow" style="left:88px;top:2450px" viewBox="0 0 20 28"><path d="M15 3L5 14l10 11" stroke="#111" stroke-width="2.5" fill="none"/></svg>
  <svg class="abs arrow" style="left:1091px;top:2450px" viewBox="0 0 20 28"><path d="M5 3l10 11L5 25" stroke="#111" stroke-width="2.5" fill="none"/></svg>

  <div class="abs review" style="left:143px"><span class="q">“</span><span class="mark"></span><p>Such a great experience! My husband booked us the romantic flight as a suprise it was absolutely adorable. Definitely need to have a good tour guide</p><span class="q qe">”</span></div>
  <div class="abs review" style="left:451px"><span class="q">“</span><span class="mark"></span><p>This was an Early Christmas gift for my 9yr old special needs son. Everything exceeded my expectations and Marco our pilot did an amazing job .</p><span class="q qe">”</span></div>
  <div class="abs review" style="left:759px"><span class="q">“</span><span class="mark"></span><p>Great experience for a first timer! Marco was a great pilot and tour guide. Accommodated our schedule changes and easy to work with. Highly recommend!</p><span class="q qe">”</span></div>

  <div class="abs person" style="left:143px"><div class="avatar" role="img" aria-label="Reviewer portrait"></div><div><b>Marisol Vega</b><span class="stars">★★★★★</span></div></div>
  <div class="abs person" style="left:451px"><div class="avatar" role="img" aria-label="Reviewer portrait"></div><div><b>Tomas Reyes</b><span class="stars">★★★★★</span></div></div>
  <div class="abs person" style="left:759px"><div class="avatar" role="img" aria-label="Reviewer portrait"></div><div><b>Janelle K</b><span class="stars">★★★★★</span></div></div>
</section>

<!-- FAQ -->
<section class="faq">
  <h2 class="abs title" style="top:2703px">FREQUENTLY ASKED QUESTION</h2>
  <div class="abs bar" style="top:2757px"></div>
  <div class="abs faq-item" style="top:2795px">Lorem ipsum dolor sit amet,adipiscing elit?<svg width="16" height="16" viewBox="0 0 16 16"><circle cx="8" cy="8" r="8" fill="#1f5ca8"/><path d="M6.5 4.5L10 8l-3.5 3.5" stroke="#fff" stroke-width="1.8" fill="none"/></svg></div>
  <div class="abs faq-item" style="top:2863px">Sed ut perspiciatis unde omnis iste ?<svg width="16" height="16" viewBox="0 0 16 16"><circle cx="8" cy="8" r="8" fill="#1f5ca8"/><path d="M6.5 4.5L10 8l-3.5 3.5" stroke="#fff" stroke-width="1.8" fill="none"/></svg></div>
  <div class="abs faq-item open" style="top:2929px">
    <div class="row">Duis aute irure dolor in reprehenderit in voluptate?<svg width="16" height="16" viewBox="0 0 16 16"><circle cx="8" cy="8" r="8" fill="#fff"/><path d="M4.5 6.5L8 10l3.5-3.5" stroke="#1f5ca8" stroke-width="1.8" fill="none"/></svg></div>
    <p>Sed ut perspiciatis unde omnis iste natus error voluptatem accusantium doloremque laudantium, totam rem aperiam, eaque ipsa quae ab illo inventore veritatis et uasi architecto beatae vitae dicta sunt explicabo.</p>
  </div>
  <div class="abs faq-item" style="top:3057px">Nemo enim ipsam voluptatem quia voluptas?<svg width="16" height="16" viewBox="0 0 16 16"><circle cx="8" cy="8" r="8" fill="#1f5ca8"/><path d="M6.5 4.5L10 8l-3.5 3.5" stroke="#fff" stroke-width="1.8" fill="none"/></svg></div>
  <p class="abs more"><span>HAVE MORE QUESTIONS?</span> ›</p>
</section>

<!-- Contact -->
<section>
  <div class="abs contact"></div>
  <div class="abs watermark" aria-hidden="true">SP</div>
  <h2 class="abs title" style="top:3287px">CONTACT US</h2>
  <div class="abs bar" style="top:3341px"></div>
  <div class="abs field" style="top:3391px">Full Name *</div>
  <div class="abs field" style="top:3457px">Phone Number *</div>
  <div class="abs field" style="top:3523px">Email Address *</div>
  <div class="abs field msg" style="top:3391px">Message *</div>
  <div class="abs btn" style="left:520px;top:3614px;width:160px;height:43px">SUBMIT NOW <svg class="chev" viewBox="0 0 7 10"><path d="M1 1l4 4-4 4" stroke="#fff" stroke-width="1.6" fill="none"/></svg></div>
</section>

<!-- Footer -->
<footer>
  <svg class="abs site-footer" viewBox="0 0 1200 330" width="1200" height="330"><path d="M0 50 Q600 -30 1200 50 L1200 330 L0 330 Z" fill="#0d0d0d"/></svg>
  <div class="abs footer-brand">skyPARLOR</div>
  <div class="abs fcol" style="left:400px;top:3788px"><h5>Quick Links</h5><ul><li>Visit Our Blog</li><li>About Us</li><li>Careers</li></ul></div>
  <div class="abs fcol" style="left:567px;top:3788px"><h5>Hotline Hours</h5><ul>
    <li>Mon 09:00 am – 05:30 pm</li><li>Tue 09:00 am – 05:30 pm</li><li>Wed 09:00 am – 05:30 pm</li><li>Thu 09:00 am – 05:30 pm</li><li>Fri 09:00 am – 05:30 pm</li><li>Sat 09:00 am – 05:30 pm</li><li>Sun 10:00 am – 03:00 pm</li></ul></div>
  <div class="abs fcol" style="left:801px;top:3788px"><h5>Contact Us</h5>
    <div class="ci"><span class="ring"><svg width="11" height="11" viewBox="0 0 24 24"><path fill="#e8e8e8" d="M6.6 10.8a15 15 0 0 0 6.6 6.6l2.2-2.2a1 1 0 0 1 1-.25 11 11 0 0 0 3.6.6 1 1 0 0 1 1 1V20a1 1 0 0 1-1 1A17 17 0 0 1 3 4a1 1 0 0 1 1-1h3.5a1 1 0 0 1 1 1 11 11 0 0 0 .6 3.6 1 1 0 0 1-.25 1z"/></svg></span><li>(844) 555-0192 | (844) 555-0148</li></div>
    <div class="ci"><span class="ring"><svg width="11" height="9" viewBox="0 0 13 10"><rect width="13" height="10" rx="1" fill="#e8e8e8"/><path d="M0 1l6.5 5L13 1" stroke="#0d0d0d" fill="none"/></svg></span><li>info@skyparlor-example.com</li></div>
    <h5 style="margin-top:10px">Follow Us</h5>
    <div class="socials"><i></i><i></i><i></i></div>
  </div>
  <p class="abs copyright">© 2026 Copyright - skyPARLOR. All Rights Reserved.</p>
</footer>

</body>
</html>
```